Animal Eye Clinic needs a Business card

We are a new veterinary ophthalmology practice (Ridgeline Pet Vision Care) and we need a business card designed. We only see animal eyes - we are not a regular veterinary clinic. We already have a logo. We are looking for a professional, good looking business card to hand out to our clients. We are looking for something simple but professional and contemporary. Our logo is likely the only picture/graphic that needs to be on the card.
Updates

Contact Information for Business Card

Delia Vossman, BSc, DVM, MSc, DipACVO
Veterinary Ophthalmologist

Phone: 250.418.3927
Email: ridgelinepetvisioncare@mailbox-example.net
Website: ridgelinepetvisioncare-example.net
Address: 1874 Thornbury Rd
Kelowna, BC, V1X 4M9

Colors

Designer to choose colors to be used in the design.

Requirements
Must have
• Our logo (attached)

```html
<!DOCTYPE html>
<html lang="en">
<head>
<meta charset="utf-8">
<title>Ridgeline Pet Vision Care – Business Card</title>
<link href="https://fonts.googleapis.com/css2?family=Lato:wght@400;700;900&display=swap" rel="stylesheet">
<style>
  :root {
    --backdrop: #5f5f5f;
    --card: #050607;
    --teal: #1b9aaa;
    --text: #e6e6e6;
    --muted: #9a9a9a;
  }
  * { box-sizing: border-box; margin: 0; padding: 0; }
  html, body {
    width: 1200px; height: 900px; overflow: hidden;
    background: var(--backdrop);
    font-family: "Lato", sans-serif;
  }
  .card {
    position: absolute;
    width: 540px; height: 309px;
    background: var(--card);
    border: 1px solid var(--teal);
    box-shadow: 0 0 0 5px var(--card), 0 0 0 6px var(--teal), 0 18px 30px rgba(0,0,0,.45);
  }
  .card--front { left: 610px; top: 110px; }
  .card--back  { left: 50px;  top: 470px; }

  /* front */
  .brand {
    position: absolute; left: 70px; top: 110px;
    display: flex; align-items: center; gap: 16px;
  }
  .brand__dot {
    width: 46px; height: 46px; border-radius: 50%;
    background: var(--teal);
  }
  .brand__name {
    color: var(--teal); font-weight: 900;
    font-size: 30px; letter-spacing: .5px; line-height: 1;
  }
  .website {
    position: absolute; font-size: 12px; letter-spacing: 1.2px;
    color: var(--text);
  }
  .website span { color: var(--teal); }
  .card--front .website { left: 70px; bottom: 36px; }

  /* back */
  .person { position: absolute; left: 34px; top: 70px; width: 200px; text-align: right; }
  .person__name { color: var(--teal); font-weight: 900; font-size: 25px; line-height: 1.1; }
  .person__creds { color: var(--text); font-size: 8px; margin-top: 3px; letter-spacing: .3px; }
  .person__title { color: var(--text); font-size: 13px; margin-top: 4px; }
  .divider {
    position: absolute; left: 250px; top: 66px; width: 1px; height: 92px;
    background: var(--teal);
  }
  .contact { position: absolute; left: 264px; top: 66px; color: var(--text); font-size: 12.5px; line-height: 1.4; }
  .contact__company { color: var(--teal); font-weight: 700; font-size: 13.5px; }
  .contact__row { display: flex; align-items: center; gap: 7px; font-size: 11.5px; }
  .contact__row svg { width: 11px; height: 11px; flex: none; }
  .card--back .website { left: 34px; bottom: 36px; }
</style>
</head>
<body>
  <section class="card card--front" aria-label="Card front">
    <div class="brand">
      <div class="brand__dot"></div>
      <div class="brand__name">RIDGELINE PET<br>VISION CARE</div>
    </div>
    <p class="website">www.<span>ridgelinepetvisioncare-example.net</span></p>
  </section>

  <section class="card card--back" aria-label="Card back">
    <div class="person">
      <h1 class="person__name">Delia Vossman</h1>
      <p class="person__creds">BSc, DVM, MSc, DipACVO</p>
      <p class="person__title">Veterinary Ophthalmologist</p>
    </div>
    <div class="divider"></div>
    <div class="contact">
      <p class="contact__company">Ridgeline Pet Vision Care</p>
      <p>1874 Thornbury Rd</p>
      <p>Kelowna, BC, V1X 4M9</p>
      <p class="contact__row">
        <svg viewBox="0 0 24 24" aria-hidden="true"><path fill="#1b9aaa" d="M6.6 10.8a15 15 0 0 0 6.6 6.6l2.2-2.2a1 1 0 0 1 1-.25 11.4 11.4 0 0 0 3.6.57 1 1 0 0 1 1 1V20a1 1 0 0 1-1 1A17 17 0 0 1 3 4a1 1 0 0 1 1-1h3.5a1 1 0 0 1 1 1c0 1.25.2 2.45.57 3.6a1 1 0 0 1-.25 1z"/></svg>
        250.418.3927
      </p>
      <p class="contact__row">
        <svg viewBox="0 0 24 24" aria-hidden="true"><rect x="2" y="5" width="20" height="14" rx="1.5" fill="#1b9aaa"/><path d="M3 6l9 7 9-7" fill="none" stroke="#050607" stroke-width="1.8"/></svg>
        ridgelinepetvisioncare@mailbox-example.net
      </p>
    </div>
    <p class="website">www.<span>ridgelinepetvisioncare-example.net</span></p>
  </section>
</body>
</html>
```